German Headhunter/ HR Consultancy needs Business Cards Design

We need a business Card Design for our Company in Stuttgart. We are specialized as Headhunter/ HR Consultancy in Placement of specialist and managers in permanent employment. Please refer to our business logo.

```html
<!DOCTYPE html>
<html lang="de">
<head>
<meta charset="utf-8">
<title>Kernwerk Personalberatung – Visitenkarte</title>
<link rel="stylesheet" href="https://fonts.googleapis.com/css2?family=Questrial&family=Roboto:wght@400&display=swap">
<style>
  :root {
    --brand-blue: #3a56a6;
    --edge-grey: #8c9098;
    --frost-light: #f6f4f4;
    --frost-mid: #dcd8d8;
    --frost-blush: #ead2d4;
    --ink-white: #ffffff;
    --page-bg: #e8e6e5;
  }
  * { margin: 0; padding: 0; box-sizing: border-box; }
  html, body {
    width: 1200px;
    height: 900px;
    overflow: hidden;
    background: var(--page-bg);
  }
  .business-card {
    position: absolute;
    left: 100px;
    top: 141px;
    width: 1000px;
    height: 618px;
    overflow: hidden;
    box-shadow: 0 14px 40px rgba(0, 0, 0, 0.18);
  }
  .card-surface {
    position: absolute;
    inset: 0;
    width: 100%;
    height: 100%;
  }
  .contact-block {
    position: absolute;
    left: 59px;
    top: 122px;
    color: var(--ink-white);
    font-family: "Roboto", Arial, sans-serif;
  }
  .person-name {
    font-family: "Questrial", "Century Gothic", sans-serif;
    font-size: 41px;
    letter-spacing: 0.5px;
    line-height: 1;
    font-weight: 400;
    -webkit-text-stroke: 0.8px var(--ink-white);
  }
  .person-role {
    font-size: 27px;
    line-height: 1.2;
    margin-top: 4px;
  }
  .postal-address {
    font-style: normal;
    font-size: 27px;
    line-height: 37px;
    margin-top: 52px;
  }
  .contact-list {
    list-style: none;
    margin-top: 30px;
    font-size: 27px;
    line-height: 37px;
  }
  .contact-list li {
    display: flex;
    align-items: center;
    gap: 9px;
  }
  .contact-icon {
    width: 27px;
    height: 27px;
    flex: none;
  }
  .brand-mark {
    position: absolute;
    left: 545px;
    top: 252px;
    display: flex;
    align-items: center;
    gap: 22px;
    color: var(--brand-blue);
    font-family: "Questrial", "Century Gothic", sans-serif;
    font-weight: 400;
  }
  .brand-square {
    width: 58px;
    height: 58px;
    background: var(--brand-blue);
    flex: none;
  }
  .brand-name {
    display: flex;
    flex-direction: column;
    line-height: 1;
  }
  .brand-name-main {
    font-size: 56px;
    letter-spacing: 1px;
  }
  .brand-name-sub {
    font-size: 25px;
    letter-spacing: 0.6px;
    margin-top: 4px;
  }
</style>
</head>
<body>
  <main class="business-card">
    <svg class="card-surface" viewBox="0 0 1000 618" preserveAspectRatio="none" aria-hidden="true">
      <defs>
        <linearGradient id="frost" x1="0" y1="0" x2="1" y2="1">
          <stop offset="0" stop-color="var(--frost-light)"/>
          <stop offset="0.35" stop-color="var(--frost-blush)"/>
          <stop offset="0.6" stop-color="var(--frost-mid)"/>
          <stop offset="1" stop-color="var(--frost-light)"/>
        </linearGradient>
      </defs>
      <rect class="frosted-panel" x="0" y="0" width="1000" height="618" fill="url(#frost)" role="img" aria-label="Frosted clear card finish"/>
      <polygon class="blue-panel" points="0,0 680,0 372,306 663,618 0,618" fill="var(--brand-blue)"/>
      <polyline class="panel-edge" points="683,0 376,306 667,618" fill="none" stroke="var(--edge-grey)" stroke-width="6"/>
    </svg>

    <section class="contact-block">
      <h1 class="person-name">LUKAS BRENNER</h1>
      <p class="person-role">Geschäftsführer</p>
      <address class="postal-address">
        Königstraße 48,<br>
        Innenstadt<br>
        70173, Stuttgart
      </address>
      <ul class="contact-list">
        <li>
          <svg class="contact-icon" viewBox="0 0 24 24" aria-hidden="true">
            <path d="M6.6 3.5l3 3.4-1.8 2.2c1.2 2.6 3.3 4.7 5.9 5.9l2.2-1.8 3.4 3-1.6 3.3C10.8 19.3 4.7 13.2 3.3 6.2z" fill="none" stroke="#fff" stroke-width="1.8" stroke-linejoin="round"/>
            <path d="M14 5.5a5 5 0 0 1 4.5 4.5M14 2a8.5 8.5 0 0 1 8 8" fill="none" stroke="#fff" stroke-width="1.6" stroke-linecap="round"/>
          </svg>
          <span>0711-555 208 417</span>
        </li>
        <li>
          <svg class="contact-icon" viewBox="0 0 24 24" aria-hidden="true">
            <rect x="2" y="5" width="20" height="14" fill="#fff"/>
            <path d="M2 5l10 8 10-8" fill="none" stroke="var(--brand-blue)" stroke-width="1.8"/>
          </svg>
          <span>kontakt@kernwerk-hr.de</span>
        </li>
        <li>
          <svg class="contact-icon" viewBox="0 0 24 24" aria-hidden="true">
            <g fill="none" stroke="#fff" stroke-width="1.6">
              <circle cx="12" cy="12" r="9.5"/>
              <ellipse cx="12" cy="12" rx="4.2" ry="9.5"/>
              <path d="M2.5 12h19M4 7h16M4 17h16"/>
            </g>
          </svg>
          <span>www.kernwerk-hr.de</span>
        </li>
      </ul>
    </section>

    <div class="brand-mark">
      <span class="brand-square" aria-hidden="true"></span>
      <p class="brand-name">
        <span class="brand-name-main">KERNWERK</span>
        <span class="brand-name-sub">PERSONALBERATUNG</span>
      </p>
    </div>
  </main>
</body>
</html>
```